Property Services Company Needs a Brochure Design

Looking for a new brochure design for an existing property services company.

We provide a range of property services from, market research, real estate brokerage, valuation and appraisal, property development and other real estate consulting services.

We would like a fresh modern brochure design with good graphics and features. Our colours are white, blue and orange.

The design should communicate, attention to detail, superior service delivery and distinction in results.
Updates

I would like the brochure to be roughly about 20 pages.

Containing the following,

1) An introduction
2) Contents Page
2) What we do
3) Our Services
4) Agency & Brokerage
5) Real Estate Consulting
6) Market Research
7) Appraisal & Valuation
8) Project Management
9) Property Development

I would also like icons to represent items 4,5,6,7,8 & 9, they should be represented vertically on each of the pages from the contents page and highlighted individually on the pages that they represent.. i.e. on appraisal & valuation page, all six icons will be arranged vertically and the appraisal and valuations icon will be highlighted.

I will also like to have images that depict the services on the various pages.

I have some pages I think will flow which I will upload shortly.

Industry/Entity Type

Real Estate

Font styles to use
Serif

Colors
f78f20
0455a3

```html
<!DOCTYPE html>
<html lang="en">
<head>
<meta charset="utf-8">
<title>Corvell Property Services – Brochure Cover</title>
<link rel="stylesheet" href="https://fonts.googleapis.com/css2?family=Arimo:wght@400;700&family=Open+Sans:wght@500&display=swap">
<style>
  :root {
    --blue: #4b46a2;
    --blue-light: #5a58b0;
    --navy: #2b2a78;
    --orange: #e66a26;
    --white: #ffffff;
    --sky: #8fb8e0;
  }
  * { margin: 0; padding: 0; box-sizing: border-box; }
  html, body { width: 1200px; height: 869px; overflow: hidden; background: #ffffff; }
  .brochure {
    position: relative; width: 1200px; height: 869px; overflow: hidden;
    background: var(--white);
    font-family: "Arimo", Arial, sans-serif; color: var(--white);
  }
  .blue-field {
    position: absolute; inset: 0;
    background: linear-gradient(100deg, var(--blue) 0%, #4540a0 55%, var(--blue-light) 100%);
    clip-path: polygon(0 498px, 601px 392px, 1200px 293px, 1200px 869px, 0 869px);
  }
  .team-photo {
    position: absolute; left: 0; top: 0; width: 601px; height: 500px;
    background: linear-gradient(160deg, var(--sky) 0%, #b9d3ea 35%, #d9d37a 65%, #9fc58e 100%);
    clip-path: polygon(0 0, 601px 0, 601px 392px, 0 498px);
  }
  .brand { position: absolute; display: flex; align-items: center; font-family: "Open Sans", Arial, sans-serif; font-weight: 500; color: var(--navy); }
  .brand-mark { background: var(--orange); flex: none; }
  .brand-text { display: flex; flex-direction: column; line-height: 1; }
  .brand--small { left: 24px; top: 30px; gap: 8px; }
  .brand--small .brand-mark { width: 14px; height: 14px; }
  .brand--small .brand-name { font-size: 28px; }
  .brand--small .brand-sub { font-size: 10px; margin-top: 3px; margin-left: 18px; }
  .brand--large { left: 643px; top: 85px; gap: 12px; }
  .brand--large .brand-mark { width: 22px; height: 22px; }
  .brand--large .brand-name { font-size: 46px; }
  .brand--large .brand-sub { font-size: 17px; margin-top: 6px; margin-left: 30px; }
  .interiors { position: absolute; left: 0; top: 0; }
  .tagline {
    position: absolute; left: 630px; top: 606px;
    font-size: 26px; letter-spacing: 0.3px; display: flex; align-items: center;
  }
  .tagline .divider { width: 2px; height: 34px; background: var(--orange); margin: 0 6px 0 10px; }
  .intro {
    position: absolute; left: 630px; top: 660px; width: 344px;
    font-size: 14.6px; line-height: 19px; text-align: justify;
  }
  .contact { position: absolute; left: 48px; top: 664px; list-style: none; font-size: 15px; line-height: 19px; }
  .contact li { display: flex; gap: 8px; margin-bottom: 0; }
  .contact svg { width: 11px; height: 13px; flex: none; margin-top: 3px; }
  .footer-band {
    position: absolute; left: 0; bottom: 0; width: 1200px; height: 45px;
    background: var(--orange); font-size: 16.5px; display: flex; align-items: center;
  }
  .footer-web { position: absolute; left: 42px; }
  .footer-call { position: absolute; left: 630px; }
  .footer-call strong { font-weight: 700; font-size: 18px; margin-left: 14px; }
</style>
</head>
<body>
<main class="brochure">
  <div class="team-photo" role="img" aria-label="Photo of three site engineers in hard hats reviewing building plans outdoors"></div>
  <div class="blue-field"></div>

  <div class="brand brand--small">
    <span class="brand-mark"></span>
    <span class="brand-text"><span class="brand-name">Corvell</span><span class="brand-sub">Property Services</span></span>
  </div>

  <div class="brand brand--large">
    <span class="brand-mark"></span>
    <span class="brand-text"><span class="brand-name">Corvell</span><span class="brand-sub">Property Services</span></span>
  </div>

  <svg class="interiors" width="1200" height="520" viewBox="0 0 1200 520">
    <defs>
      <linearGradient id="officeTone" x1="0" y1="0" x2="1" y2="1">
        <stop offset="0" stop-color="#f2f4f6"/><stop offset="0.6" stop-color="#c9ced3"/><stop offset="1" stop-color="#8e949a"/>
      </linearGradient>
      <linearGradient id="lobbyTone" x1="0" y1="0" x2="1" y2="1">
        <stop offset="0" stop-color="#d9d2c3"/><stop offset="0.5" stop-color="#b9ae98"/><stop offset="1" stop-color="#8c8270"/>
      </linearGradient>
    </defs>
    <polygon role="img" aria-label="Photo of a bright modern office with desk and chair" points="638,282 896,243 896,440 638,483" fill="url(#officeTone)" stroke="var(--orange)" stroke-width="5" stroke-linejoin="miter"/>
    <polygon role="img" aria-label="Photo of a polished marble lobby interior" points="907,195 1165,155 1165,355 907,397" fill="url(#lobbyTone)" stroke="var(--orange)" stroke-width="5" stroke-linejoin="miter"/>
  </svg>

  <h2 class="tagline">Detail<span class="divider"></span>Delivery<span class="divider"></span>Distinction</h2>
  <p class="intro">We enjoy long-standing relationships with many of our clients and landlords, our lettings teams are always happy to meet with new clients to advise them on how best to maximise their rental return.</p>

  <ul class="contact">
    <li>
      <svg viewBox="0 0 12 14"><path d="M6 0a5 5 0 0 1 5 5c0 3.5-5 9-5 9S1 8.5 1 5a5 5 0 0 1 5-5zm0 3a2 2 0 1 0 0 4 2 2 0 0 0 0-4z" fill="#fff"/></svg>
      <span>9th Floor, Harbour Court,<br>58 Marina Road Lagos,<br>Nigeria</span>
    </li>
    <li>
      <svg viewBox="0 0 12 14"><path d="M4 1C2 2 2 5 3 8s3 5 5 5l1-2-2-1-1 1C5 10 4 8 4 6l1-1-1-3z" fill="#fff"/></svg>
      <span>+234 1 5550142</span>
    </li>
    <li>
      <svg viewBox="0 0 12 14"><rect x="3" y="2" width="6" height="3" fill="#fff"/><rect x="1" y="5" width="10" height="6" rx="1" fill="#fff"/></svg>
      <span>+234 1 5550187</span>
    </li>
    <li>
      <svg viewBox="0 0 12 14"><rect x="1" y="4" width="10" height="7" fill="none" stroke="#fff" stroke-width="1.2"/><path d="M1 4l5 4 5-4" fill="none" stroke="#fff" stroke-width="1.2"/></svg>
      <span>info@corvellprop.com.ng</span>
    </li>
  </ul>

  <footer class="footer-band">
    <span class="footer-web">For More Information Visit: www.corvellprop.com.ng</span>
    <span class="footer-call">Call Us Today <strong>+234 1 5550142</strong></span>
  </footer>
</main>
</body>
</html>
```